Business Card Design

New business card design

Target Market(s)

Residential & Commercial Property Managers

Industry/Entity Type

Plumbing Services

Contact Information for Business Card

Name - Rowan Keddle, title - Director, Phone Number - 0431 286 517, email - rowan@tbk-plumbing.com.au, Company ABN - 73 215 904 386,

Font styles to use
Sans Serif

Colors
0054AA
0677BA
7BADD7
CADEEF
E8F1F8

```html
<!DOCTYPE html>
<html lang="en">
<head>
<meta charset="utf-8">
<title>TBK Plumbing Services – Business Card</title>
<link rel="stylesheet" href="https://fonts.googleapis.com/css2?family=Arimo:wght@400;700&display=swap">
<style>
  :root {
    --page-bg: #ececec;
    --card-navy: #1d2129;
    --card-navy-light: #3e4450;
    --accent-blue: #14a0e3;
    --text-white: #ffffff;
    --text-grey: #8a8f99;
    --divider: #6b717c;
    --swoosh-white: #ffffff;
  }
  * { margin: 0; padding: 0; box-sizing: border-box; }
  html, body {
    width: 1200px; height: 900px; overflow: hidden;
    background: var(--page-bg);
    font-family: "Arimo", Arial, sans-serif;
  }
  .sheet {
    position: relative; width: 1200px; height: 900px;
    display: flex; flex-direction: column; align-items: center; justify-content: center; gap: 50px;
  }
  .card {
    position: relative; width: 630px; height: 360px;
    border-radius: 26px; overflow: hidden;
    background: var(--card-navy);
    box-shadow: 0 10px 24px rgba(0,0,0,0.18);
  }
  .card-swoosh { position: absolute; inset: 0; width: 100%; height: 100%; }
  .brand { position: absolute; color: var(--text-white); text-align: center; }
  .brand-name {
    font-size: 84px; font-weight: 400; line-height: 1; letter-spacing: 2px;
    display: flex; align-items: center; justify-content: center; gap: 12px;
  }
  .brand-dot {
    width: 14px; height: 14px; border-radius: 50%; background: var(--accent-blue);
  }
  .brand-tagline {
    margin-top: 8px; font-size: 11px; letter-spacing: 6px; color: var(--text-grey);
    text-transform: lowercase;
  }
  .card-front .brand { left: 40px; top: 78px; width: 250px; }
  .front-divider {
    position: absolute; left: 300px; top: 95px; width: 1px; height: 170px; background: var(--divider);
  }
  .contact { position: absolute; left: 320px; top: 112px; color: var(--text-white); }
  .contact-name {
    font-size: 27px; font-weight: 700; color: var(--accent-blue); text-transform: uppercase; letter-spacing: 0.5px;
  }
  .contact-title { font-size: 18px; margin-top: 2px; }
  .contact-line { font-size: 18px; margin-top: 8px; display: flex; align-items: center; gap: 8px; }
  .contact-line .label { color: var(--accent-blue); }
  .contact-line svg { width: 15px; height: 15px; fill: var(--accent-blue); flex: none; }
  .contact-abn { margin-top: 12px; }
  .back-pattern { position: absolute; inset: 0;
    background: linear-gradient(150deg, #14171d 0%, #1d2129 45%, #353a44 100%); }
  .card-back .brand { left: 0; right: 0; top: 128px; }
</style>
</head>
<body>
<main class="sheet">
  <section class="card card-front" aria-label="Business card front">
    <svg class="card-swoosh" viewBox="0 0 630 360" preserveAspectRatio="none" aria-hidden="true">
      <path d="M0,232 C170,312 400,348 630,358 L630,360 L0,360 Z" fill="var(--accent-blue)"/>
      <path d="M0,250 C170,322 400,354 590,360 L0,360 Z" fill="var(--swoosh-white)"/>
      <path d="M0,326 C90,344 210,354 340,360 L0,360 Z" fill="var(--accent-blue)"/>
    </svg>
    <div class="brand">
      <div class="brand-name">tbk<span class="brand-dot"></span></div>
      <div class="brand-tagline">plumbing services</div>
    </div>
    <div class="front-divider"></div>
    <div class="contact">
      <div class="contact-name">Rowan Keddle</div>
      <div class="contact-title">Director</div>
      <div class="contact-line contact-abn"><span class="label">ABN:</span> 73 215 904 386</div>
      <div class="contact-line">
        <svg viewBox="0 0 24 24" aria-hidden="true"><path d="M6.6 10.8a15 15 0 0 0 6.6 6.6l2.2-2.2a1 1 0 0 1 1-.25 11.4 11.4 0 0 0 3.6.57 1 1 0 0 1 1 1V20a1 1 0 0 1-1 1A17 17 0 0 1 3 4a1 1 0 0 1 1-1h3.5a1 1 0 0 1 1 1c0 1.25.2 2.45.57 3.57a1 1 0 0 1-.25 1z"/></svg>
        0431 286 517
      </div>
      <div class="contact-line">
        <svg viewBox="0 0 24 24" aria-hidden="true"><path d="M2 6a2 2 0 0 1 2-2h16a2 2 0 0 1 2 2v12a2 2 0 0 1-2 2H4a2 2 0 0 1-2-2zm2 .5v.3l8 5 8-5v-.3zm0 2.6V18h16V9.1l-8 5z"/></svg>
        rowan@tbk-plumbing.com.au
      </div>
    </div>
  </section>

  <section class="card card-back" aria-label="Business card back">
    <div class="back-pattern" role="img" aria-label="Embossed water-drop pattern in dark charcoal tones"></div>
    <div class="brand">
      <div class="brand-name">tbk<span class="brand-dot"></span></div>
      <div class="brand-tagline">plumbing services</div>
    </div>
  </section>
</main>
</body>
</html>
```